Personal Motivational Quote Poster Design

I would like to create a poster with some of my favorite quotes to hang in my office. I did similar projects in 2012 and 2014. I've uploaded the winning designs so you can get a better idea of what I'm looking for. I will provide feedback on your design within 24 hours of receiving it.

The poster must contain the following quotes:

“What the pupil must learn, if he learns anything at all, is that the world will do most of the work for you, provided you cooperate with it by identifying how it really works and aligning with those realities. If we do not let the world teach us, it teaches us a lesson.” - Harold Quenby

“I tackle every big new problem by asking two questions: Who has dealt with this problem well? And what can we learn from them?” - Walt Prisco

“If we can really understand the problem, the answer will come out of it, because the answer is not separate from the problem.” - Ravindra Selvapathi

“Success is nothing more than a few simple disciplines, practiced every day; while failure is simply a few errors in judgment, repeated every day. It is the accumulative weight of our disciplines and our judgments that leads us to either fortune or failure.” - Ned Falco

“Inaction breeds doubt and fear. Action breeds confidence and courage.” - Rufus Pembrook

“What’s the one thing you can do, such that by doing it, everything else will be easier or unnecessary?” - Lyle Dorsey

Requirements
Must have
• The poster will be 24" high x 36" long and printed on canvas, so the image you create needs to have a resolution of at least 2700 x 3900.
Nice to have
• I don't have an exact vision for how the poster should look, so I am totally open to you using your creativity to develop, arrange and present the content as you'd like.

That said, I would like an image (photo or posterized image) of the person being quoted along with each quote. I do not have specific images that I would like you to use, so you will need to find the images on your own.

The images don't need to be perfect... I am more interested in the poster relating the essence of the quotes and the people being quoted than I am in perfect photographic images of the people being quoted.

```html
<!DOCTYPE html>
<html lang="en">
<head>
<meta charset="utf-8">
<title>Quote Poster</title>
<link rel="stylesheet" href="https://fonts.googleapis.com/css2?family=Delius&family=Handlee&display=swap">
<style>
  :root {
    --paper: #ffffff;
    --ink: #1a1a1a;
    --peach: #f7c4a8;
    --sage: #e1ebcb;
    --taupe: #d4bfab;
    --sand: #e6d0b8;
    --mist: #dcdcdc;
    --portrait-a: #c9c9c9;
    --portrait-b: #a9a9a9;
    --frame: #111111;
  }
  html, body { margin: 0; padding: 0; overflow: hidden; background: var(--paper); }
  .poster {
    position: relative; width: 1200px; height: 800px; overflow: hidden;
    background: var(--paper); color: var(--ink);
    font-family: "Delius", "Comic Sans MS", sans-serif;
  }
  .backdrop { position: absolute; inset: 0; }
  .quote { position: absolute; margin: 0; font-size: 21px; line-height: 1.3; }
  .quote .big { font-size: 31px; }
  .quote .mid { font-size: 28px; }
  .quote span.big, .quote span.mid, .quote span.lead { line-height: 1; }
  .author {
    position: absolute; margin: 0; font-family: "Handlee", cursive;
    font-size: 19px; line-height: 1.2; white-space: nowrap;
  }
  .justify { text-align: justify; text-align-last: justify; }
  .right { text-align: right; }

  .q-quenby { left: 50px; top: 62px; width: 528px; }
  .q-quenby p { margin: 0; }
  .q-quenby .lesson { margin-top: 4px; line-height: 1.15; }
  .a-quenby { left: 56px; top: 248px; }

  .q-pembrook { left: 620px; top: 58px; width: 511px; line-height: 40px; white-space: nowrap; font-size: 19px; }
  .q-pembrook .lead { font-size: 28px; }
  .a-pembrook { left: 960px; top: 192px; width: 171px; text-align: right; }

  .q-falco { left: 628px; top: 266px; width: 505px; line-height: 1.32; }
  .a-falco { left: 990px; top: 498px; width: 143px; text-align: right; }

  .q-prisco { left: 60px; top: 318px; width: 520px; line-height: 40px; }
  .a-prisco { left: 66px; top: 458px; }

  .q-selvapathi { left: 55px; top: 530px; width: 540px; line-height: 38px; }
  .a-selvapathi { left: 60px; top: 670px; }

  .q-dorsey { left: 638px; top: 540px; width: 507px; line-height: 1.35; }
  .a-dorsey { left: 990px; top: 656px; width: 155px; text-align: right; }
</style>
</head>
<body>
<main class="poster">
  <svg class="backdrop" width="1200" height="800" viewBox="0 0 1200 800">
    <defs>
      <linearGradient id="portrait-fade" x1="0" y1="0" x2="0" y2="1">
        <stop offset="0" stop-color="var(--portrait-a)" stop-opacity="0"/>
        <stop offset="1" stop-color="var(--portrait-b)" stop-opacity="0.75"/>
      </linearGradient>
    </defs>
    <rect class="block-peach" x="19" y="38" width="602" height="260" fill="var(--peach)"/>
    <polygon class="block-sage" points="613,57 1176,33 1185,247 620,257" fill="var(--sage)"/>
    <rect class="block-taupe" x="599" y="256" width="582" height="270" fill="var(--taupe)"/>
    <polygon class="block-sand" points="31,514 610,505 612,713 33,723" fill="var(--sand)"/>
    <rect class="block-mist" x="594" y="526" width="591" height="244" fill="var(--mist)"/>
    <rect x="19" y="600" width="591" height="170" fill="url(#portrait-fade)"
          role="img" aria-label="Faded portraits of Harold Quenby, Walt Prisco and Ravindra Selvapathi"/>
    <rect x="594" y="600" width="591" height="170" fill="url(#portrait-fade)"
          role="img" aria-label="Faded portraits of Rufus Pembrook, Ned Falco and Lyle Dorsey"/>
    <g fill="none" stroke="var(--frame)" stroke-width="2.5">
      <polygon class="frame-quenby" points="45,24 639,71 618,326 25,281"/>
      <rect class="frame-pembrook" x="610" y="36" width="547" height="204"/>
      <polygon class="frame-falco" points="595,240 1180,276 1172,540 587,505"/>
      <rect class="frame-prisco" x="34" y="307" width="592" height="187" fill="var(--paper)"/>
      <polygon class="frame-selvapathi" points="21,535 606,472 627,668 41,732"/>
      <polygon class="frame-dorsey" points="607,539 1175,527 1180,741 613,752"/>
    </g>
  </svg>

  <blockquote class="quote q-quenby">
    <p class="justify">&ldquo;&nbsp;&nbsp;&nbsp;What the pupil must learn, if he learns anything at all, is that the world will do most of the work for you, provided you cooperate with it by identifying how it really works and aligning with those realities.</p>
    <p class="lesson big justify">&nbsp;If we do not let the world teach us, it</p>
    <p class="lesson big">teaches us a lesson.&rdquo;</p>
  </blockquote>
  <p class="author a-quenby">- Harold Quenby</p>

  <blockquote class="quote q-pembrook right">
    <span class="lead">Inaction</span> breeds <span class="lead">doubt and fear.</span><br>
    <span class="lead">Action</span> breeds <span class="lead">confidence and courage.&rdquo;</span>
  </blockquote>
  <p class="author a-pembrook">- Rufus Pembrook</p>

  <blockquote class="quote q-falco">
    <div class="justify">&ldquo;<span class="big">Success</span> is nothing more than a few simple disciplines, practiced every day; while <span class="big">failure</span> is simply a few errors in judgment, repeated every day. It is the accumulative weight of <span class="mid">our disciplines and our judgments</span> that <span class="mid">leads us to either</span></div>
    <div class="right mid">fortune or failure.&rdquo;</div>
  </blockquote>
  <p class="author a-falco">- Ned Falco</p>

  <blockquote class="quote q-prisco">
    &ldquo;I tackle every big new problem by asking two<br>
    questions: <span class="big">Who</span> has dealt with this problem well?<br>
    And <span class="big">what</span> can we learn from them?&rdquo;
  </blockquote>
  <p class="author a-prisco">- Walt Prisco</p>

  <blockquote class="quote q-selvapathi">
    &ldquo;If we can really understand the problem, the answer<br>
    will come out of it, because <span class="big">the answer is not</span><br>
    <span class="big">separate from the problem.&rdquo;</span>
  </blockquote>
  <p class="author a-selvapathi">- Ravindra Selvapathi</p>

  <blockquote class="quote q-dorsey">
    <div class="justify">&ldquo;What&rsquo;s <span class="big">the one thing you can do,</span></div>
    <div class="justify">such that by doing it, everything else will be easier</div>
    <div class="right">or unnecessary?&rdquo;</div>
  </blockquote>
  <p class="author a-dorsey">- Lyle Dorsey</p>
</main>
</body>
</html>
```